Lawn Sign For Construction Projects - Brisk Harbor

This contest is for a lawn sign that will be placed in the front yard of recently completed construction projects. The goal here is to have a bold advertising sign that is visible from a vehicle driving past.

We are still deciding on the default size for our sign, we also may use multiple sizes. The two sizes we will more than likely be using are: 18"h x 24"w and 24"h x 36"w.

Preference will be given to designers that submit original designs that tie into our current brand and are either in both the size formats listed above or are easy to scale in photoshop or illustrator.

In the files, you will see our logo and an example of a lawn sign.

Please contact us with any questions or comments you may have!

Thank You,
- The Brisk Harbor Team
Updates

Project Deadline Extended Reason: We Currently to not have any designs worth choosing. Added Monday, March 21, 2016

Industry/Entity Type

Residential Construction

Colors
34a7d8
ffffff
faa54b

Requirements
Nice to have
• 1. The sign must tie into our current branding and color scheme.
• 2. The sign must be clearly visible and readable.
• 3. The sign must include our phone number in readable print.
• 4. Our website written in small print along the bottom of the sign.
• 5. Must mention we install the following products:
• a.) Solar
• b.) Roofing
• c.) Windows
• d.) Artificial Lawn
• e.) Whole House Fans
• f.) Patio Covers

```html
<!DOCTYPE html>
<html lang="en">
<head>
<meta charset="utf-8">
<title>Brisk Harbor Lawn Sign</title>
<link href="https://fonts.googleapis.com/css2?family=Montserrat:wght@700&family=Open+Sans:wght@400;700&family=Roboto+Slab:wght@800&family=Arimo:wght@400;700&display=swap" rel="stylesheet">
<style>
  :root {
    --backdrop: #e9ebee;
    --paper: #ffffff;
    --charcoal: #3d3d3d;
    --orange: #f7941d;
    --orange-deep: #e8742a;
    --blue: #1f6fb8;
    --ink: #1a1a1a;
  }
  * { margin: 0; padding: 0; box-sizing: border-box; }
  html, body { width: 1051px; height: 1200px; overflow: hidden; background: var(--backdrop); }
  .canvas { position: relative; width: 1051px; height: 1200px; }
  .sign {
    position: absolute; left: 87px; top: 15px; width: 876px; height: 1169px;
    background: var(--paper); overflow: hidden;
  }
  .sign-shapes { position: absolute; inset: 0; width: 100%; height: 100%; }
  .brand-dot {
    position: absolute; left: 238px; top: 41px; width: 120px; height: 120px;
    border: 12px solid var(--orange-deep); border-radius: 50%;
  }
  .brand-name {
    position: absolute; left: 0; width: 592px; top: 212px; text-align: center;
    font-family: "Montserrat", sans-serif; font-weight: 700; font-size: 70px;
    line-height: 1; color: var(--blue); letter-spacing: -1px;
  }
  .website {
    position: absolute; left: 0; width: 592px; top: 307px; transform: translateY(-50%);
    text-align: center; font-family: "Open Sans", sans-serif; font-size: 27px; color: var(--ink);
  }
  .install-heading {
    position: absolute; left: 43px; top: 422px; transform: translateY(-50%);
    font-family: "Roboto Slab", serif; font-weight: 800; font-size: 35px; color: var(--ink);
  }
  .product { position: absolute; transform: translateY(-50%); display: flex; align-items: center; }
  .product-tick { width: 56px; height: 56px; flex: none; }
  .product-name {
    position: absolute; white-space: nowrap;
    font-family: "Arimo", sans-serif; font-size: 64px; color: var(--blue); line-height: 1;
  }
  .phone {
    position: absolute; right: 16px; top: 1062px; transform: translateY(-50%);
    font-family: "Arimo", sans-serif; font-weight: 700; font-size: 70px; color: var(--orange);
    letter-spacing: -1px;
  }
  .address {
    position: absolute; right: 37px; top: 1124px; transform: translateY(-50%);
    font-family: "Open Sans", sans-serif; font-weight: 700; font-size: 21px; color: var(--orange-deep);
  }
</style>
</head>
<body>
<div class="canvas">
  <div class="sign">
    <svg class="sign-shapes" viewBox="0 0 565 754" preserveAspectRatio="none" aria-hidden="true">
      <polygon points="352,0 565,0 565,378" fill="var(--charcoal)"/>
      <polygon points="380,110 402,104 565,393 565,439" fill="var(--orange)"/>
      <polygon points="0,375 0,754 212,754" fill="var(--charcoal)"/>
      <polygon points="50,464 72,454 244,754 214,754" fill="var(--orange)"/>
    </svg>

    <div class="brand-dot"></div>
    <div class="brand-name">BRISK HARBOR</div>
    <div class="website">www.briskharbor-build.com</div>

    <div class="install-heading">WE INSTALL</div>

    <div class="product" style="left:43px; top:507px;">
      <svg class="product-tick" viewBox="0 0 40 40" aria-hidden="true"><rect x="3" y="14" width="22" height="22" fill="none" stroke="var(--blue)" stroke-width="2.5"/><polyline points="7,22 14,32 37,3" fill="none" stroke="var(--orange-deep)" stroke-width="4" stroke-linejoin="round"/></svg>
      <span class="product-name" style="left:126px;">Whole House Fans</span>
    </div>
    <div class="product" style="left:99px; top:589px;">
      <svg class="product-tick" viewBox="0 0 40 40" aria-hidden="true"><rect x="3" y="14" width="22" height="22" fill="none" stroke="var(--blue)" stroke-width="2.5"/><polyline points="7,22 14,32 37,3" fill="none" stroke="var(--orange-deep)" stroke-width="4" stroke-linejoin="round"/></svg>
      <span class="product-name" style="left:129px;">Artificial Lawn</span>
    </div>
    <div class="product" style="left:163px; top:670px;">
      <svg class="product-tick" viewBox="0 0 40 40" aria-hidden="true"><rect x="3" y="14" width="22" height="22" fill="none" stroke="var(--blue)" stroke-width="2.5"/><polyline points="7,22 14,32 37,3" fill="none" stroke="var(--orange-deep)" stroke-width="4" stroke-linejoin="round"/></svg>
      <span class="product-name" style="left:124px;">Patio Covers</span>
    </div>
    <div class="product" style="left:220px; top:750px;">
      <svg class="product-tick" viewBox="0 0 40 40" aria-hidden="true"><rect x="3" y="14" width="22" height="22" fill="none" stroke="var(--blue)" stroke-width="2.5"/><polyline points="7,22 14,32 37,3" fill="none" stroke="var(--orange-deep)" stroke-width="4" stroke-linejoin="round"/></svg>
      <span class="product-name" style="left:124px;">Windows</span>
    </div>
    <div class="product" style="left:281px; top:832px;">
      <svg class="product-tick" viewBox="0 0 40 40" aria-hidden="true"><rect x="3" y="14" width="22" height="22" fill="none" stroke="var(--blue)" stroke-width="2.5"/><polyline points="7,22 14,32 37,3" fill="none" stroke="var(--orange-deep)" stroke-width="4" stroke-linejoin="round"/></svg>
      <span class="product-name" style="left:124px;">Roofing</span>
    </div>
    <div class="product" style="left:336px; top:913px;">
      <svg class="product-tick" viewBox="0 0 40 40" aria-hidden="true"><rect x="3" y="14" width="22" height="22" fill="none" stroke="var(--blue)" stroke-width="2.5"/><polyline points="7,22 14,32 37,3" fill="none" stroke="var(--orange-deep)" stroke-width="4" stroke-linejoin="round"/></svg>
      <span class="product-name" style="left:126px;">Solar</span>
    </div>

    <div class="phone">(555) 318-2047</div>
    <div class="address">2870 Alder Ct. Ste 12 Fairview, CA 95810</div>
  </div>
</div>
</body>
</html>
```